Stylish Business Cards Wanted

- DOUBLE SIDED Design Required -

High end, edgy cards for a corporate and personal stylist. Must include logo,
Name: Belinda Harwick
Title: Director and Stylist
telephone : +61 8 7142 5809
email: belinda@theloombriefing.example
website: theloombriefing.example
Tag: Corporate Workwear & Uniform Specialist | Personal Stylist
Would like nice icons for telephone, email, website

Target Market(s)

Businesses wanting stylish uniforms, people wanting stylish wardrobes

Industry/Entity Type

Corporate Workwear Stylist

Contact Information for Business Card

I would like black, white and gold foiling incorporated in the design - possibly a touch of the other colours on my branding guide attached Name: Belinda Harwick Title: Director and Stylist telephone : +61 8 7142 5809 email: belinda@theloombriefing.example website: theloombriefing.example Tag: Corporate Workwear & Uniform Specialist | Personal Stylist Would like nice icons for telephone, email, website

Font styles to use
Other font styles liked:
• Raleway

Colors

Designer to choose colors to be used in the design.

Requirements
Must have
• Gold foil accents

```html
<!DOCTYPE html>
<html lang="en">
<head>
<meta charset="utf-8">
<title>The Loom Briefing – Business Cards</title>
<link href="https://fonts.googleapis.com/css2?family=Roboto:wght@400;500&family=Raleway:wght@600&family=Yellowtail&display=swap" rel="stylesheet">
<style>
  :root {
    --backdrop: #3b3b3d;
    --card: #1d1d1f;
    --gold: #d6a92e;
    --white: #f4f4f4;
    --muted: #e2e2e2;
  }
  html, body {
    margin: 0;
    padding: 0;
    width: 799px;
    height: 1200px;
    overflow: hidden;
    background: var(--backdrop);
  }
  .canvas {
    position: relative;
    width: 799px;
    height: 1200px;
  }
  .card {
    position: absolute;
    left: 100px;
    width: 600px;
    height: 345px;
    background: var(--card);
    border-radius: 22px;
    box-shadow: 0 14px 30px rgba(0,0,0,0.45);
    overflow: hidden;
  }
  .card--front { top: 135px; }
  .card--back { top: 720px; }

  .brand-name {
    font-family: "Raleway", sans-serif;
    font-weight: 600;
    text-transform: uppercase;
    letter-spacing: 0.14em;
    margin: 0;
    line-height: 1;
  }
  .card--front .brand-name {
    position: absolute;
    left: 0; right: 0;
    top: 150px;
    text-align: center;
    font-size: 40px;
    color: var(--gold);
  }
  .card--back .brand-name {
    position: absolute;
    right: 40px;
    bottom: 52px;
    font-size: 22px;
    color: var(--white);
  }

  .holder {
    position: absolute;
    left: 42px;
    top: 40px;
  }
  .holder-name {
    font-family: "Yellowtail", cursive;
    font-size: 34px;
    color: var(--gold);
    margin: 0;
    line-height: 1.1;
  }
  .holder-title {
    font-family: "Roboto", sans-serif;
    font-size: 13px;
    color: var(--muted);
    margin: 2px 0 0 2px;
  }

  .contact-list {
    position: absolute;
    left: 42px;
    bottom: 50px;
    margin: 0;
    padding: 0;
    list-style: none;
    font-family: "Roboto", sans-serif;
    font-size: 15px;
    color: var(--white);
  }
  .contact-item {
    display: flex;
    align-items: center;
    gap: 12px;
    margin-top: 9px;
  }
  .contact-icon {
    width: 14px;
    height: 14px;
    flex: none;
  }
</style>
</head>
<body>
<main class="canvas">
  <section class="card card--front" aria-label="Card front">
    <h1 class="brand-name">The Loom Briefing</h1>
  </section>

  <section class="card card--back" aria-label="Card back">
    <div class="holder">
      <p class="holder-name">Belinda Harwick</p>
      <p class="holder-title">Director and Stylist</p>
    </div>

    <ul class="contact-list">
      <li class="contact-item">
        <svg class="contact-icon" viewBox="0 0 16 16" aria-hidden="true">
          <circle cx="8" cy="8" r="7" fill="none" stroke="var(--gold)" stroke-width="1.3"/>
          <path d="M5.4 4.6l1.3 1.6-.7.9c.5 1 1.3 1.8 2.3 2.3l.9-.7 1.6 1.3-.7 1.1c-2.6-.4-4.6-2.4-5-5z" fill="var(--gold)"/>
        </svg>
        <span>+61 8 7142 5809</span>
      </li>
      <li class="contact-item">
        <svg class="contact-icon" viewBox="0 0 16 16" aria-hidden="true">
          <rect x="1.5" y="3.5" width="13" height="9" rx="1" fill="none" stroke="var(--gold)" stroke-width="1.3"/>
          <path d="M2 4l6 5 6-5" fill="none" stroke="var(--gold)" stroke-width="1.3"/>
        </svg>
        <span>belinda@theloombriefing.example</span>
      </li>
      <li class="contact-item">
        <svg class="contact-icon" viewBox="0 0 16 16" aria-hidden="true">
          <circle cx="8" cy="8" r="7" fill="var(--gold)"/>
          <ellipse cx="8" cy="8" rx="3" ry="7" fill="none" stroke="var(--card)" stroke-width="1"/>
          <path d="M1 8h14M2.5 4.5h11M2.5 11.5h11" stroke="var(--card)" stroke-width="1"/>
        </svg>
        <span>www.theloombriefing.example</span>
      </li>
    </ul>

    <p class="brand-name">The Loom Briefing</p>
  </section>
</main>
</body>
</html>
```